Working Capital graphics

Our business advisory firm requires 9 images to be re-created and improved in the branding of our business.

The 9 images have been uploaded below and the colours and branding of the business can be found at the website www.tallowmereadvisory.com.au

```html
<!DOCTYPE html>
<html lang="en">
<head>
<meta charset="utf-8">
<title>Working Capital Levers Along the Value Chain</title>
<link href="https://fonts.googleapis.com/css2?family=Ubuntu:wght@500;700&display=swap" rel="stylesheet">
<style>
  :root {
    --navy: #1b3a8c;
    --orange: #f7941d;
    --blue: #0db2f0;
    --white: #ffffff;
  }
  html, body {
    margin: 0;
    padding: 0;
    width: 1200px;
    height: 652px;
    overflow: hidden;
    background: var(--white);
  }
  .value-chain {
    display: block;
    width: 1200px;
    height: 652px;
    font-family: "Ubuntu", Arial, sans-serif;
  }
  .connector { stroke: var(--navy); stroke-width: 2; fill: none; }
  .stage-fill { fill: var(--white); }
  .ring-left { stroke: var(--orange); stroke-width: 3.5; fill: none; }
  .ring-right { stroke: var(--blue); stroke-width: 3.5; fill: none; }
  .stage-label { fill: var(--navy); font-weight: 700; text-anchor: middle; }
  .lever-payable { fill: var(--orange); }
  .lever-receivable { fill: var(--blue); }
  .lever-label { fill: var(--white); font-weight: 700; text-anchor: middle; }
  .legend-label { fill: var(--navy); font-weight: 700; font-size: 11px; }
</style>
</head>
<body>
<svg class="value-chain" viewBox="0 0 1200 652" xmlns="http://www.w3.org/2000/svg" role="img" aria-label="Working capital levers along the value chain">
  <defs>
    <g id="stage-ring">
      <circle class="stage-fill" r="46"/>
      <path class="ring-left" d="M0,-46 A46,46 0 0 0 0,46"/>
      <path class="ring-right" d="M0,-46 A46,46 0 0 1 0,46"/>
    </g>
  </defs>

  <!-- connectors -->
  <g class="connectors">
    <line class="connector" x1="114" y1="355" x2="1094" y2="355"/>
    <line class="connector" x1="114" y1="275" x2="114" y2="309"/>
    <line class="connector" x1="359" y1="158" x2="359" y2="182"/>
    <line class="connector" x1="359" y1="275" x2="359" y2="309"/>
    <line class="connector" x1="359" y1="401" x2="359" y2="436"/>
    <polyline class="connector" points="236,309 236,294 482,294 482,275"/>
    <line class="connector" x1="788" y1="275" x2="788" y2="355"/>
    <line class="connector" x1="971" y1="158" x2="971" y2="182"/>
    <line class="connector" x1="971" y1="275" x2="971" y2="309"/>
    <line class="connector" x1="971" y1="401" x2="971" y2="436"/>
    <line class="connector" x1="1094" y1="275" x2="1094" y2="309"/>
    <line class="connector" x1="1094" y1="401" x2="1094" y2="436"/>
  </g>

  <!-- value chain stages -->
  <g class="stages">
    <g transform="translate(114,355)"><use href="#stage-ring"/><text class="stage-label" font-size="14" y="5">DESIGN</text></g>
    <g transform="translate(236,355)"><use href="#stage-ring"/><text class="stage-label" font-size="13.5"><tspan x="0" y="-10">ORDER/</tspan><tspan x="0" y="5">MATERIAL</tspan><tspan x="0" y="20">PLANNING</tspan></text></g>
    <g transform="translate(359,355)"><use href="#stage-ring"/><text class="stage-label" font-size="12" y="4">PURCHASING</text></g>
    <g transform="translate(482,355)"><use href="#stage-ring"/><text class="stage-label" font-size="9.5" y="4">MANUFACTURING</text></g>
    <g transform="translate(604,355)"><use href="#stage-ring"/><text class="stage-label" font-size="11.5" y="4">PRE-ASSEMBLY</text></g>
    <g transform="translate(726,355)"><use href="#stage-ring"/><text class="stage-label" font-size="12" y="4">ASSEMBLY</text></g>
    <g transform="translate(849,355)"><use href="#stage-ring"/><text class="stage-label" font-size="11.5"><tspan x="0" y="-3">PACKAGING/</tspan><tspan x="0" y="10">SHIPPING</tspan></text></g>
    <g transform="translate(971,355)"><use href="#stage-ring"/><text class="stage-label" font-size="13.5" y="5">SALES</text></g>
    <g transform="translate(1094,355)"><use href="#stage-ring"/><text class="stage-label" font-size="11"><tspan x="0" y="-3">AFTER SALES/</tspan><tspan x="0" y="10">SERVICE</tspan></text></g>
  </g>

  <!-- levers -->
  <g class="levers">
    <g transform="translate(114,228)"><circle class="lever-payable" r="47"/><text class="lever-label" font-size="10.5"><tspan x="0" y="-8">REDUCE PART</tspan><tspan x="0" y="4">VARIANTS/</tspan><tspan x="0" y="16">RELEASES</tspan></text></g>
    <g transform="translate(359,112)"><circle class="lever-receivable" r="47"/><text class="lever-label" font-size="12.5"><tspan x="0" y="-11">MODIFY</tspan><tspan x="0" y="4">PAYMENT</tspan><tspan x="0" y="19">CONDITIONS</tspan></text></g>
    <g transform="translate(359,228)"><circle class="lever-receivable" r="47"/><text class="lever-label" font-size="12.5"><tspan x="0" y="-11">OPTIMIZE</tspan><tspan x="0" y="4">PAYMENT</tspan><tspan x="0" y="19">PROCESSES</tspan></text></g>
    <g transform="translate(482,228)"><circle class="lever-payable" r="47"/><text class="lever-label" font-size="9"><tspan x="0" y="-20">RETHINK</tspan><tspan x="0" y="-9">DELIVERY</tspan><tspan x="0" y="3">SCHEDULES</tspan><tspan x="0" y="14">AND</tspan><tspan x="0" y="26">WAREHOUSING</tspan></text></g>
    <g transform="translate(359,482)"><circle class="lever-payable" r="47"/><text class="lever-label" font-size="10.5"><tspan x="0" y="-9">OPTIMIZE</tspan><tspan x="0" y="4">EXTERNAL</tspan><tspan x="0" y="17">PURCHASING</tspan></text></g>
    <g transform="translate(788,228)"><circle class="lever-payable" r="47"/><text class="lever-label" font-size="12.5"><tspan x="0" y="-11">OPTIMIZE</tspan><tspan x="0" y="4">PRODUCT</tspan><tspan x="0" y="19">TESTING</tspan></text></g>
    <g transform="translate(971,112)"><circle class="lever-receivable" r="47"/><text class="lever-label" font-size="12.5"><tspan x="0" y="-11">IMPROVE</tspan><tspan x="0" y="4">PAYMENT</tspan><tspan x="0" y="19">SCHEMES</tspan></text></g>
    <g transform="translate(971,228)"><circle class="lever-receivable" r="47"/><text class="lever-label" font-size="10.5"><tspan x="0" y="-8">REDUCE DUE/</tspan><tspan x="0" y="4">OVERDUE</tspan><tspan x="0" y="16">RECEIVABLE</tspan></text></g>
    <g transform="translate(971,482)"><circle class="lever-payable" r="47"/><text class="lever-label" font-size="10.5"><tspan x="0" y="-17">REDUCE</tspan><tspan x="0" y="-4">FINISHED</tspan><tspan x="0" y="9">GOODS</tspan><tspan x="0" y="22">STOCKS</tspan></text></g>
    <g transform="translate(1094,228)"><circle class="lever-receivable" r="47"/><text class="lever-label" font-size="9.5"><tspan x="0" y="-7">ESTABLISH NEW</tspan><tspan x="0" y="4">PAYMENT</tspan><tspan x="0" y="15">CONDITIONS</tspan></text></g>
    <g transform="translate(1094,482)"><circle class="lever-payable" r="47"/><text class="lever-label" font-size="11"><tspan x="0" y="-3">REDUCE</tspan><tspan x="0" y="10">INVENTORY</tspan></text></g>
  </g>

  <!-- legend -->
  <g class="legend">
    <g transform="translate(750,573)">
      <circle class="stage-fill" r="8"/>
      <path class="ring-left" style="stroke-width:1" d="M0,-8 A8,8 0 0 0 0,8"/>
      <path class="ring-right" style="stroke-width:1" d="M0,-8 A8,8 0 0 1 0,8"/>
    </g>
    <text class="legend-label" x="765" y="577">INVENTORY</text>
    <circle class="lever-payable" cx="850" cy="573" r="9"/>
    <text class="legend-label"><tspan x="869" y="577">PAYABLES AND</tspan><tspan x="869" y="589">PRE-PAYMENTS MADE</tspan></text>
    <circle class="lever-receivable" cx="1003" cy="573" r="9"/>
    <text class="legend-label"><tspan x="1021" y="577">RECEIVABLES AND</tspan><tspan x="1021" y="589">PRE-PAYMENTS RECEIVED</tspan></text>
  </g>
</svg>
</body>
</html>
```